NEW Modern Sleek Business Card for VR Language Startup

Our startup is using VR to lead the next wave of world language education. We need a two-sided business card that introduces the larger organization (Brightloom Language Inc) and our contact info on one side and shows the product, Glimwoorld, on the other side.

Side 1 (contact info)= Brightloom Logo and Contact info (name, title, phone, email)

Side 2 (product)= Glimworld logo, text, and website
Text= Culturally Immersive Language Learning Games
Website= www.glimworld-play.com

Target Market(s)

Education, Technology

Contact Information for Business Card

Contact info will be updated upon approval of the design. For now, put this as a placeholder.

Perry Dunmore
Founder & CEO
pdunmore@quillpost-mail.net
(555)-014-2286

Font styles to use
Other font styles liked:
• Gibson and Century Gothic are the brand fonts

Requirements
Nice to have
• I would love to see cohesion between the design and colors of the two logos. I have attached a few business card designs that I like, so you can get a feel for my preferred style.

```html
<!DOCTYPE html>
<html lang="en">
<head>
<meta charset="utf-8">
<title>Brightloom Language – Business Card</title>
<link rel="stylesheet" href="https://fonts.googleapis.com/css2?family=Didact+Gothic&family=Outfit:wght@400;600;700&display=swap">
<style>
  :root {
    --bg: #1d1d22;
    --card: #ffffff;
    --ink: #1a1a1a;
    --ink-soft: #555555;
    --ink-muted: #6b6b6b;
    --product-blue: #4a6fd8;
    --wash-blue: #dbeef8;
    --wash-violet: #e4e0f4;
    --wash-peach: #fde3d6;
    --wash-lilac: #e9e2f4;
    --icon-a: #e0457b;
    --icon-b: #6a5ad6;
  }
  * { box-sizing: border-box; margin: 0; padding: 0; }
  html, body { width: 1200px; height: 800px; overflow: hidden; background: var(--bg); }
  .stage {
    width: 1200px; height: 800px;
    display: flex; align-items: center; justify-content: center; gap: 70px;
  }
  .card {
    position: relative;
    width: 340px; height: 560px;
    background: var(--card);
    border-radius: 26px;
    overflow: hidden;
    font-family: "Didact Gothic", "Century Gothic", sans-serif;
  }
  .card__wash {
    position: absolute; left: 0; right: 0; bottom: 0; height: 300px;
  }
  .card--product .card__wash {
    background: linear-gradient(180deg, rgba(255,255,255,0) 0%, var(--wash-blue) 45%, var(--wash-violet) 100%);
  }
  .card--contact .card__wash {
    background: linear-gradient(180deg, rgba(255,255,255,0) 0%, var(--wash-peach) 45%, var(--wash-lilac) 100%);
  }
  .brand {
    position: absolute; display: flex; align-items: center; gap: 12px;
    font-family: "Outfit", sans-serif; font-weight: 700;
  }
  .brand__dot { width: 14px; height: 14px; border-radius: 50%; flex: none; }
  /* product side */
  .card--product .brand {
    top: 64px; right: 34px; font-size: 44px; color: var(--product-blue);
  }
  .card--product .brand__dot { background: var(--product-blue); }
  .tagline {
    position: absolute; top: 190px; left: 38px;
    font-size: 26px; line-height: 1.3; color: var(--ink-muted);
  }
  .website {
    position: absolute; top: 340px; left: 38px;
    font-size: 19px; color: var(--ink-soft);
  }
  /* contact side */
  .card--contact .brand {
    top: 60px; left: 34px; flex-direction: column; align-items: flex-start; gap: 6px;
    color: var(--ink); font-size: 36px; letter-spacing: 4px; line-height: 1;
  }
  .card--contact .brand__sub { letter-spacing: 11px; font-size: 22px; }
  .person { position: absolute; top: 270px; left: 38px; }
  .person__name {
    font-family: "Outfit", sans-serif; font-weight: 700;
    font-size: 21px; letter-spacing: 1px; color: var(--ink); text-transform: uppercase;
  }
  .person__title { font-size: 17px; color: var(--ink-soft); margin-top: 4px; }
  .contact-list { list-style: none; margin-top: 22px; }
  .contact-list li {
    display: flex; align-items: center; gap: 9px;
    font-size: 15px; color: var(--ink-soft); margin-bottom: 9px;
  }
  .contact-list svg { width: 18px; height: 18px; flex: none; }
</style>
</head>
<body>
<main class="stage">
  <section class="card card--product" aria-label="Glimworld product side">
    <div class="card__wash" role="img" aria-label="Soft blue and violet brand wash"></div>
    <div class="brand"><span class="brand__dot"></span>Glimworld</div>
    <p class="tagline">Culturally Immersive<br>Language<br>Learning Games</p>
    <p class="website">www.glimworld-play.com</p>
  </section>

  <section class="card card--contact" aria-label="Brightloom Language contact side">
    <div class="card__wash" role="img" aria-label="Soft peach and lilac brand wash"></div>
    <div class="brand"><span>BRIGHTLOOM</span><span class="brand__sub">LANGUAGE</span></div>
    <div class="person">
      <p class="person__name">Perry Dunmore</p>
      <p class="person__title">Founder &amp; CEO</p>
      <ul class="contact-list">
        <li>
          <svg viewBox="0 0 20 20" aria-hidden="true"><circle cx="10" cy="10" r="10" fill="var(--icon-a)"/><path d="M6.5 5.5h2l1 2.5-1.3 1a6 6 0 0 0 2.8 2.8l1-1.3 2.5 1v2a1 1 0 0 1-1 1A8.5 8.5 0 0 1 5.5 6.5a1 1 0 0 1 1-1z" fill="#fff"/></svg>
          (555)-014-2286
        </li>
        <li>
          <svg viewBox="0 0 20 20" aria-hidden="true"><circle cx="10" cy="10" r="10" fill="var(--icon-b)"/><rect x="5" y="6.5" width="10" height="7" rx="1" fill="#fff"/><path d="M5.3 7l4.7 3.6L14.7 7" stroke="var(--icon-b)" stroke-width="1.2" fill="none"/></svg>
          pdunmore@quillpost-mail.net
        </li>
      </ul>
    </div>
  </section>
</main>
</body>
</html>
```